Halvik - consultancy website

I need a new design for my webpage/presence [to be functioning with Wordpress - I have a programmer to set it up but not the design idea].
My company is Halvik - a consultancy firm focused on growth management for Swedish SME's primarily;. We call it Leadership toolkit for firms on the rise, kind of a doctor helping small become big. Contentwise, its a simple frontpage + 3-4 subpages with content re company/myself/focus etc. The new site should communicate a fresh, trustworthy take yet simple and functional on all devices [i.e. think UI compatible for mobile/tablet]. Current building parts/form elements are
a) existing logo and text elements
b) existing pictures
c) the yellowish color
colours and new ideas on pictures/positioning are welcome. I prefer a 'full width page' solution with centralised text elements but that's all up to you to suggest. Current site is a quickfix made by myself - now I'm moving it to a new platform so want to take the opportunity to make it
Nothing superspecial as it is a 2-man show; on the other hand I still want to have a modern & fresh reflection of my brand in digital environments. Help me out!
www.halvik-demo.se
Best
Lina Bergqvist

```html
<!DOCTYPE html>
<html lang="en">
<head>
<meta charset="utf-8">
<title>Halvik – Services</title>
<link href="https://fonts.googleapis.com/css2?family=Arimo:wght@400;700&family=PT+Serif:wght@400&display=swap" rel="stylesheet">
<style>
:root{
  --accent:#e38f2b;
  --ink:#222222;
  --muted:#6b6b6b;
  --line:#e2e2e2;
  --dot:#8a8a8a;
  --bar:#2b2b2b;
  --band:#333333;
  --footer:#1c1c1c;
  --base:#111111;
  --fb:#3b5a9a;
  --tw:#3aa9e0;
  --gp:#dd4b39;
  --white:#ffffff;
}
*{margin:0;padding:0;box-sizing:border-box}
html,body{width:782px;height:1200px;overflow:hidden;background:var(--white)}
body{position:relative;font-family:"Arimo",Arial,sans-serif;color:var(--ink)}
.abs{position:absolute}

/* header */
.site-header{position:absolute;left:0;top:0;width:782px;height:86px}
.brand{left:64px;top:16px}
.brand-name{font-family:"PT Serif",Georgia,serif;font-size:34px;line-height:1;color:var(--ink);letter-spacing:.5px}
.brand-tagline{font-family:"PT Serif",Georgia,serif;font-size:10px;color:var(--ink);margin-top:4px;padding-left:2px}
.main-nav{top:39px;font-size:9.6px;color:var(--ink)}
.main-nav a{position:absolute;color:inherit;text-decoration:none;white-space:nowrap}
.main-nav a.active{color:var(--accent)}
.nav-underline{left:527px;top:56px;width:70px;height:1px;background:var(--accent)}

/* breadcrumb */
.breadcrumb{left:0;top:86px;width:782px;height:35px;background:var(--bar);font-size:9.2px;color:var(--white);padding:13px 0 0 64px}
.breadcrumb .sep{margin:0 5px}
.breadcrumb .current{color:var(--accent);font-weight:700}

/* intro */
.section-title{left:0;top:164px;width:782px;text-align:center;font-size:17px;font-weight:700}
.intro{left:62px;top:200px;width:658px;text-align:center;font-size:9px;line-height:13.4px;color:var(--muted)}

/* timeline */
.timeline-rail{left:391px;top:277px;width:1px;height:525px;background:var(--line)}
.dot{width:8px;height:8px;border-radius:50%;background:var(--dot)}
.service-title{font-size:17px;line-height:20px;color:var(--ink)}
.service-title b{font-weight:700}
.service-title.accent{color:var(--accent)}
.service-text{font-size:9px;line-height:13.4px;color:var(--muted);width:295px}
.left{text-align:right}

/* cta band */
.cta{left:0;top:835px;width:782px;height:183px;background:var(--band);color:var(--white);text-align:center}
.cta-head{position:absolute;left:0;top:50px;width:782px;font-size:20px;font-weight:700;letter-spacing:3px}
.cta-sub{position:absolute;left:0;top:78px;width:782px;font-size:8.6px;font-weight:700;letter-spacing:1.4px}
.cta-btn{position:absolute;left:339px;top:108px;width:105px;height:27px;border:1.5px solid var(--white);border-radius:2px;font-size:8.8px;font-weight:700;line-height:24px}

/* footer */
.site-footer{left:0;top:1018px;width:782px;height:149px;background:var(--footer);color:var(--white)}
.footer-head{position:absolute;top:24px;font-size:9.6px}
.col-divider{position:absolute;top:27px;width:1px;height:102px;background:#3a3a3a}
.social{position:absolute;top:56px;width:47px;height:61px;text-align:center}
.social .disc{width:24px;height:24px;border-radius:50%;background:rgba(255,255,255,.18);margin:10px auto 0}
.social .count{font-size:8.2px;margin-top:9px}
.fb{left:64px;background:var(--fb)}
.tw{left:116px;background:var(--tw)}
.gp{left:168px;background:var(--gp)}
.mail-copy{position:absolute;left:349px;top:52px;font-size:7.4px;line-height:12.5px;color:#a8a8a8}
.mail-input{position:absolute;left:349px;top:85px;width:130px;height:18px;background:#f4f4f4;font-size:6.8px;color:#aaa;padding:5px 0 0 10px;letter-spacing:.4px}
.mail-submit{position:absolute;left:479px;top:85px;width:21px;height:18px;background:var(--accent)}
.mail-note{position:absolute;left:349px;top:110px;font-size:7px;color:#8a8a8a}
.footer-menu{position:absolute;left:633px;top:53px;list-style:none;font-size:7.5px;line-height:13.9px}

.base{left:0;top:1167px;width:782px;height:33px;background:var(--base);text-align:center;font-size:7.4px;color:#666;padding-top:12px}
</style>
</head>
<body>

<header class="site-header">
  <div class="abs brand">
    <div class="brand-name">Halvik.</div>
    <div class="brand-tagline">Leadership toolkit for firms on the rise</div>
  </div>
  <nav class="abs main-nav" style="left:0">
    <a style="left:400px">Home</a>
    <a style="left:467px">About Us</a>
    <a class="active" style="left:540px">Services</a>
    <a style="left:618px">Gallery</a>
    <a style="left:681px">Contact Us</a>
  </nav>
  <div class="abs nav-underline"></div>
</header>

<div class="abs breadcrumb">Home<span class="sep">&gt;&gt;</span><span class="current">Services</span></div>

<h1 class="abs section-title">Our Services</h1>
<p class="abs intro">Donec eu viverra odio, eu cursus orci. Vestibulum id imperdiet est, non dictum leo. Aenean dictum nunc ex, quis vehicula dolor posuere id. Donec luctus luctus nisl, id porta turpis. Class aptent taciti sociosqu ad litora torquent per conubia nostra, per inceptos himenaeos. Curabitur metus libero, suscipit pretium erat sed, cursus faucibus erat. Vestibulum ante ipsum primis in</p>

<div class="abs timeline-rail"></div>

<svg class="abs" style="left:377px;top:298px" width="28" height="28" viewBox="0 0 28 28" aria-hidden="true">
  <circle cx="14" cy="14" r="12.5" fill="#fff" stroke="var(--accent)" stroke-width="1"/>
  <circle cx="14" cy="14" r="7.5" fill="var(--accent)"/>
</svg>
<div class="abs dot" style="left:387px;top:450px"></div>
<div class="abs dot" style="left:387px;top:567px"></div>
<div class="abs dot" style="left:387px;top:705px"></div>

<h2 class="abs service-title accent left" style="right:423px;top:293px;font-weight:400">Growth<br><b>Management</b></h2>
<p class="abs service-text left" style="left:64px;top:349px">Pellentesque feugiat lacus a leo faucibus facilisis. Sed non tristique massa. Integer molestie, nunc quis sollicitudin condimentum.Pellentesque feugiat lacus a leo faucibus facilisis. Sed non tristique massa. Integer molestie, nunc quis sollicitudin condimentum.</p>

<h2 class="abs service-title" style="left:420px;top:434px;font-weight:400">Corporate<br><b>Communication</b></h2>
<p class="abs service-text" style="left:420px;top:490px">Pellentesque feugiat lacus a leo faucibus facilisis. Sed non tristique massa. Integer molestie, nunc quis sollicitudin condimentum.Pellentesque feugiat lacus a leo faucibus facilisis. Sed non tristique massa. Integer molestie, nunc quis sollicitudin condimentum.</p>

<h2 class="abs service-title left" style="right:423px;top:550px;font-weight:400">Project<br><b>Management</b></h2>
<p class="abs service-text left" style="left:64px;top:606px">Pellentesque feugiat lacus a leo faucibus facilisis. Sed non tristique massa. Integer molestie, nunc quis sollicitudin condimentum.Pellentesque feugiat lacus a leo faucibus facilisis. Sed non tristique massa. Integer molestie, nunc quis sollicitudin condimentum.</p>

<h2 class="abs service-title" style="left:418px;top:700px"><b>Concepetualizing</b></h2>
<p class="abs service-text" style="left:420px;top:741px">Pellentesque feugiat lacus a leo faucibus facilisis. Sed non tristique massa. Integer molestie, nunc quis sollicitudin condimentum.Pellentesque feugiat lacus a leo faucibus facilisis. Sed non tristique massa. Integer molestie, nunc quis sollicitudin condimentum.</p>

<section class="abs cta">
  <div class="cta-head">DONEC EU VIVERRA ODIO, EU CURSUS ORCI.</div>
  <div class="cta-sub">IN VARIUS VENENATIS ELIT, A PLACERAT LACUS. MAURIS SUSCIPIT</div>
  <div class="cta-btn">CONTACT NOW</div>
</section>

<footer class="abs site-footer">
  <div class="footer-head" style="left:64px">Let’s Connect</div>
  <div class="social fb"><div class="disc"></div><div class="count">2598</div></div>
  <div class="social tw"><div class="disc"></div><div class="count">4576</div></div>
  <div class="social gp"><div class="disc"></div><div class="count">1269</div></div>

  <div class="col-divider" style="left:285px"></div>

  <div class="footer-head" style="left:348px">Mailing List</div>
  <p class="mail-copy">Sign up for our mailing list to get latest<br>updates and offers.</p>
  <div class="mail-input">Email address</div>
  <svg class="mail-submit" viewBox="0 0 21 18" aria-hidden="true">
    <path d="M7 9.2 9.4 11.5 14 6.5" fill="none" stroke="#fff" stroke-width="1.6" stroke-linecap="round" stroke-linejoin="round"/>
  </svg>
  <div class="mail-note">We respect your privacy</div>

  <div class="col-divider" style="left:569px"></div>

  <div class="footer-head" style="left:633px">Menu</div>
  <ul class="footer-menu">
    <li>Home</li><li>About Us</li><li>Services</li><li>Gallery</li><li>Contact Us</li>
  </ul>
</footer>

<div class="abs base">© Copyrights 2015 All Rights Reserved</div>

</body>
</html>
```